Maplecrest Disability - Social Security Disability Attorneys

Our company is expanding to attract clients nationwide for our social security disability practice. We have a logo, but I am looking for a creative and elegant letterhead that projects an image of being technologically advanced but still professional enough for the legal field. I am looking for the "wow factor" combined with this is still professional enough for a law practice.

Requesting letterhead and business card design
Updates

Had to update and change the logo. The previous logo had a typo. Please send updates with the new logo for consideration. The letterhead and business cards should be professional enough to be used for a law firm. Thanks.

Industry/Entity Type

Law Practice, Law Firm, Healthcare Industry, Government

Colors

Designer to choose colors to be used in the design.

Requirements
Nice to have
• **Please create a vertical design for the business card**

```html
<!DOCTYPE html>
<html lang="en">
<head>
<meta charset="utf-8">
<title>Maplecrest Disability – Business Card</title>
<link href="https://fonts.googleapis.com/css2?family=Arimo:wght@400;700&display=swap" rel="stylesheet">
<style>
  :root {
    --backdrop: #e4e4e2;
    --paper: #ffffff;
    --orange: #f4821f;
    --blue-deep: #3b63b3;
    --blue-mid: #2f86cc;
    --blue-bright: #27a3de;
    --ink: #333333;
    --white: #ffffff;
  }
  * { margin: 0; padding: 0; box-sizing: border-box; }
  html, body {
    width: 1200px; height: 801px; overflow: hidden;
    background: var(--backdrop);
    font-family: "Arimo", Arial, sans-serif;
  }
  .stage {
    position: relative; width: 1200px; height: 801px;
    display: flex; align-items: center; justify-content: center; gap: 40px;
  }
  .card {
    position: relative; width: 540px; height: 309px; overflow: hidden;
    box-shadow: 0 10px 24px rgba(0,0,0,.18);
  }
  .card-front { background: var(--paper); }
  .card-front .swooshes { position: absolute; inset: 0; }
  .brand-name {
    position: absolute; left: 34px; top: 120px;
    font-size: 26px; font-weight: 700; letter-spacing: .5px;
    color: var(--blue-deep); text-transform: uppercase;
    white-space: nowrap;
  }
  .holder { position: absolute; right: 48px; top: 36px; text-align: right; }
  .holder-name {
    font-size: 16px; font-weight: 700; color: var(--orange);
    letter-spacing: .5px; text-transform: uppercase;
  }
  .holder-role { font-size: 11px; color: var(--ink); margin-top: 2px; }
  .corner-tab {
    position: absolute; right: 0; top: 18px; width: 16px; height: 12px;
    background: var(--orange); border-radius: 3px 0 0 3px;
  }
  .contact-list {
    position: absolute; left: 40px; top: 196px; list-style: none;
    font-size: 11.5px; color: var(--ink); line-height: 19px;
  }
  .contact-list li { display: flex; align-items: center; gap: 8px; }
  .contact-list svg { width: 11px; height: 11px; flex: none; }
  .address-text { font-family: "Arimo", Arial, sans-serif; font-size: 11px; fill: var(--white); letter-spacing: .3px; }

  .card-back {
    background: linear-gradient(160deg, #3f66b4 0%, #2f86cc 45%, #27a3de 100%);
  }
  .card-back .sheen { position: absolute; inset: 0; }
  .card-back .brand-name {
    left: 0; right: 0; top: 134px; text-align: center;
    color: var(--white); font-size: 30px;
  }
</style>
</head>
<body>
<main class="stage">

  <section class="card card-front" aria-label="Business card front">
    <svg class="swooshes" viewBox="0 0 540 309" aria-hidden="true">
      <path d="M248 309 C285 250 330 205 372 176 C340 205 300 255 272 309 Z" fill="var(--orange)"/>
      <path d="M286 309 C330 220 420 120 540 58 L540 72 C440 130 360 215 320 309 Z" fill="var(--blue-deep)"/>
      <path d="M332 309 C380 215 450 135 540 84 L540 309 Z" fill="var(--orange)"/>
      <path id="addressLine" d="M380 300 C420 220 470 165 540 120" fill="none"/>
      <text class="address-text"><textPath href="#addressLine" startOffset="10">Your address, city, state, ZIP 0000</textPath></text>
    </svg>
    <div class="corner-tab"></div>
    <div class="holder">
      <p class="holder-name">Daniel Harper</p>
      <p class="holder-role">Manager</p>
    </div>
    <p class="brand-name">Maplecrest Disability</p>
    <ul class="contact-list">
      <li><svg viewBox="0 0 12 12"><path d="M3 1 L5 3 L4 4.5 C5 6.5 6 7.5 7.5 8 L9 7 L11 9 L9.5 11 C5 10.5 1.5 7 1 2.5 Z" fill="var(--orange)"/></svg>555-014-2763</li>
      <li><svg viewBox="0 0 12 12"><rect x="1" y="2.5" width="10" height="7" fill="none" stroke="var(--orange)" stroke-width="1.2"/><path d="M1 2.5 L6 6.5 L11 2.5" fill="none" stroke="var(--orange)" stroke-width="1.2"/></svg>youremail@mailbox.com</li>
      <li><svg viewBox="0 0 12 12"><circle cx="6" cy="6" r="5" fill="var(--orange)"/><path d="M1 6 H11 M6 1 V11 M2.5 3.5 H9.5 M2.5 8.5 H9.5" stroke="#fff" stroke-width=".7"/></svg>www.yourwebsite.com</li>
    </ul>
  </section>

  <section class="card card-back" aria-label="Business card back">
    <svg class="sheen" viewBox="0 0 540 309" aria-hidden="true">
      <path d="M0 230 C150 140 350 110 540 120 L540 150 C360 140 170 170 0 260 Z" fill="#ffffff" opacity=".12"/>
      <path d="M60 309 C200 210 380 175 540 170 L540 185 C380 195 220 235 110 309 Z" fill="#ffffff" opacity=".1"/>
      <path d="M0 160 C120 120 260 100 380 100 C260 110 130 140 0 190 Z" fill="#ffffff" opacity=".08"/>
    </svg>
    <p class="brand-name">Maplecrest Disability</p>
  </section>

</main>
</body>
</html>
```